Vindgerdi - Start-up company selling electricity

Hello let me tell you about Vindgerdi.

Vindgerdi is start-up company selling electricity in Iceland. The operations of the company consist of making power usage forecasts for our customers, purchasing the electricity wholesale from the energy producers, and selling the electricity to the consumer. We are focused on tech by using optimization and machine learning to minimize electricity prices to our customers. Our marketing strategy is to portray a tech company mindset and to show dedication to driving down the electricity price on the market.

We need your help to make our website pop. Possible concepts to work with are as follows:

- Iceland the land of ice and fire
- Green energy
- Innovation
- Tech and data science

Link to our website: https://prufa.vindgerdi-example.is/
We are open to ideas.
Thank you!

Target Market(s)

Electricity consumers both homes and companies.

Number of Pages Required

1 page

Font styles to use
Serif
Sans Serif

```html
<!DOCTYPE html>
<html lang="en">
<head>
<meta charset="utf-8">
<title>Vindgerdi – Same electricity, just cheaper</title>
<link href="https://fonts.googleapis.com/css2?family=Montserrat:wght@400;500;700;800&display=swap" rel="stylesheet">
<style>
  :root {
    --navy: #132143;
    --green: #4a8a15;
    --brand-red: #8e1d1d;
    --paper: #f5f5f7;
    --white: #ffffff;
    --ink: #0d0d0d;
    --rule: #c9c9cf;
  }
  * { margin: 0; padding: 0; box-sizing: border-box; }
  html, body { width: 936px; height: 1200px; overflow: hidden; }
  body {
    position: relative;
    background: var(--paper);
    font-family: "Montserrat", Arial, sans-serif;
    color: var(--ink);
  }
  .abs { position: absolute; white-space: nowrap; }

  /* Header */
  .site-header { position: absolute; left: 0; top: 0; width: 936px; height: 67px; background: var(--white); }
  .brand { position: absolute; display: flex; align-items: center; gap: 8px; }
  .brand-dot { width: 26px; height: 26px; border-radius: 50%; background: var(--navy); }
  .brand-name { font-weight: 700; color: var(--brand-red); letter-spacing: 0.5px; }
  .site-header .brand { left: 93px; top: 20px; }
  .site-header .brand-name { font-size: 24px; line-height: 26px; }
  .main-nav a { position: absolute; top: 26px; font-size: 10.5px; font-weight: 500; color: var(--ink); text-decoration: none; line-height: 14px; }

  /* Hero */
  .hero-visual {
    position: absolute; left: 0; top: 67px; width: 936px; height: 362px;
    background: radial-gradient(ellipse at 45% 20%, #e4f08a 0%, #a4cc3c 30%, #5f9a24 60%, #2f5a15 100%);
  }
  .hero-title { left: 354px; top: 155px; font-size: 29.5px; font-weight: 800; line-height: 36px; color: var(--ink); }
  .hero-dots { position: absolute; left: 443px; top: 379px; display: flex; gap: 13px; }
  .hero-dots span { width: 8px; height: 8px; border-radius: 50%; background: var(--white); }
  .hero-shadow { position: absolute; left: 80px; top: 432px; width: 776px; height: 6px; border-radius: 50%;
    background: radial-gradient(ellipse at center, rgba(0,0,0,0.35) 0%, rgba(0,0,0,0) 75%); }

  /* Welcome */
  .welcome-title { left: 93px; top: 463px; font-size: 29.4px; font-weight: 800; line-height: 36px; }
  .welcome-text { left: 93px; top: 506px; font-size: 11.9px; line-height: 24px; color: #222; }
  .pill { position: absolute; height: 44px; border-radius: 22px; color: var(--white); font-weight: 700;
    font-size: 15.5px; display: flex; align-items: center; justify-content: center; }
  .pill-green { background: var(--green); }
  .pill-navy { background: var(--navy); }

  /* Band */
  .pricing-panel { position: absolute; left: 0; top: 617px; width: 584px; height: 327px; background: var(--green); color: var(--white); }
  .future-panel { position: absolute; left: 584px; top: 617px; width: 352px; height: 327px; background: var(--navy); }
  .on-dark { color: var(--white); }
  .price-title { left: 93px; top: 664px; font-size: 29.5px; font-weight: 800; line-height: 36px; }
  .price-icon-box { position: absolute; left: 93px; top: 710px; width: 160px; height: 160px; background: #f7f7f8;
    display: flex; align-items: center; justify-content: center; }
  .rate { font-size: 29px; font-weight: 800; line-height: 36px; }
  .rate-unit { font-size: 12px; font-weight: 500; line-height: 16px; }
  .price-line { font-size: 19.3px; font-weight: 800; line-height: 26px; }
  .future-title { left: 614px; top: 684px; font-size: 29.7px; font-weight: 800; line-height: 38px; white-space: normal; width: 300px; }
  .future-text { left: 619px; top: 774px; font-size: 12px; line-height: 24px; white-space: normal; width: 250px; }

  /* Footer */
  .contact-item { position: absolute; left: 84px; display: flex; align-items: center; gap: 12px; font-size: 13.5px; font-weight: 500; line-height: 18px; color: var(--navy); }
  .contact-item svg { width: 14px; height: 14px; fill: var(--navy); }
  .company-info { left: 377px; top: 1016px; font-size: 13.5px; font-weight: 500; line-height: 24px; color: var(--navy); }
  .site-footer .brand { left: 626px; top: 1033px; }
  .site-footer .brand-name { font-size: 24px; line-height: 26px; }
  .version-tag { left: 887px; top: 1108px; font-size: 9px; font-weight: 700; color: var(--navy); }
  .footer-rule { position: absolute; left: 85px; top: 1133px; width: 769px; height: 1px; background: var(--rule); }
  .copyright { left: 0; width: 936px; top: 1156px; text-align: center; font-size: 13.5px; font-weight: 500; line-height: 18px; color: var(--navy); }
</style>
</head>
<body>
  <header class="site-header">
    <div class="brand"><span class="brand-dot"></span><span class="brand-name">VINDGERDI</span></div>
    <nav class="main-nav">
      <a href="#" style="left:498px">Terms of business</a>
      <a href="#" style="left:621px">Question &amp; Answer</a>
      <a href="#" style="left:752px">About Vindgerdi</a>
    </nav>
  </header>

  <section class="hero">
    <div class="hero-visual" role="img" aria-label="Cupped hands holding a small glass globe above sunlit green grass"></div>
    <h1 class="abs hero-title">Same electricity ~ just cheaper!</h1>
    <div class="hero-dots"><span></span><span></span><span></span></div>
    <div class="hero-shadow"></div>
  </section>

  <section class="welcome">
    <h2 class="abs welcome-title">Welcome to business</h2>
    <p class="abs welcome-text">Neque porro quisquam est qui dolorem ipsum quia dolor<br>sit amet, consectetur, adipisci velit...</p>
    <a class="pill pill-green" style="left:477px;top:479px;width:176px">Company</a>
    <a class="pill pill-navy" style="left:674px;top:479px;width:175px">Home</a>
  </section>

  <section class="pricing-panel"></section>
  <h2 class="abs price-title on-dark">Price list</h2>
  <div class="price-icon-box">
    <svg width="84" height="84" viewBox="0 0 84 84" aria-hidden="true">
      <circle cx="22" cy="16" r="10" fill="none" stroke="#666" stroke-width="3"/>
      <path d="M28 28 L50 22 L78 50 L60 68 L32 40 Z" fill="#666"/>
      <circle cx="34" cy="30" r="3" fill="#f7f7f8"/>
      <text x="53" y="54" font-family="Montserrat, sans-serif" font-weight="800" font-size="22" fill="#f7f7f8" text-anchor="middle" transform="rotate(45 53 46)">$</text>
    </svg>
  </div>
  <div class="abs rate on-dark" style="left:302px;top:664px">6.95</div>
  <div class="abs rate-unit on-dark" style="left:302px;top:704px">ISK / kWh</div>
  <div class="abs rate on-dark" style="left:420px;top:664px">6.22</div>
  <div class="abs rate-unit on-dark" style="left:420px;top:703px">ISK / kWh</div>
  <div class="abs price-line on-dark" style="left:301px;top:742px">electric acceleration</div>
  <div class="abs price-line on-dark" style="left:302px;top:786px">Make a price comparison</div>
  <a class="pill pill-navy" style="left:293px;top:829px;width:175px">Verdvakt</a>

  <section class="future-panel"></section>
  <h2 class="abs future-title on-dark">The future is exciting</h2>
  <p class="abs future-text on-dark">Let's make the electricity system smarter together. Vindgerdi uses artificial intelligence, data science and automation to minimize costs and promote eccentricity</p>

  <footer class="site-footer">
    <div class="contact-item" style="top:1018px">
      <svg viewBox="0 0 14 14"><path d="M7 0a5 5 0 0 0-5 5c0 3.5 5 9 5 9s5-5.5 5-9a5 5 0 0 0-5-5zm0 7a2 2 0 1 1 0-4 2 2 0 0 1 0 4z"/></svg>
      <span>Lækjarbraut 42 105 Reykjavík</span>
    </div>
    <div class="contact-item" style="top:1042px">
      <svg viewBox="0 0 14 14"><path d="M0 2h14v2L7 8 0 4z M0 5.5l7 4 7-4V12H0z"/></svg>
      <span>halló@vindgerdi-example.is</span>
    </div>
    <div class="contact-item" style="top:1066px">
      <svg viewBox="0 0 14 14"><path d="M3 0l3 3-1.5 2.5c1 2 2.5 3.5 4.5 4.5L11.5 8.5l2.5 3-2 2.5C6 13.5.5 8 0 2z"/></svg>
      <span>555-0142</span>
    </div>
    <div class="abs company-info">Vindgerdi ehf<br>ID number: 123456-7890<br>VAT number: 102938</div>
    <div class="brand"><span class="brand-dot"></span><span class="brand-name">VINDGERDI</span></div>
    <div class="abs version-tag">M1</div>
    <div class="footer-rule"></div>
    <div class="abs copyright">Copyright © Vindgerdi 2021 &nbsp;|&nbsp; All rights reserved</div>
  </footer>
</body>
</html>
```